RWT Fittings Ltd Business Cards

We need a business card with our business logo. We provide window and door installations on high-rises in west coast British Colombia, Canada.

I would like my business information and details on one side of the card, and the other side the company name with logo

Target Market(s)

General Contractors

Industry/Entity Type

Construction

Contact Information for Business Card

one side i want my company name and logo in the dark theme logo that i provided

Requirements
Must have
• Marco Peltieri, 16045518293, RWTFittings@mailbox-demo.com, 1407-5194 Linden Row Burnaby BC, V5H 2K9, Owner & Manager

```html
<!DOCTYPE html>
<html lang="en">
<head>
<meta charset="utf-8">
<title>RWT Fittings Ltd – Business Cards</title>
<link rel="stylesheet" href="https://fonts.googleapis.com/css2?family=Open+Sans:wght@400;600;700&display=swap">
<style>
  :root {
    --page: #232323;
    --card: #1f1f23;
    --photo-dark: #1c1a19;
    --photo-mid: #3b3733;
    --blue: #27a9e1;
    --grey: #9d9d9d;
    --white: #ffffff;
    --muted: #c9c9c9;
  }
  * { box-sizing: border-box; margin: 0; padding: 0; }
  html, body {
    width: 1200px; height: 780px; overflow: hidden;
    background: var(--page);
    font-family: "Open Sans", Arial, sans-serif;
  }
  .sheet {
    position: relative; width: 1200px; height: 780px;
    display: flex; align-items: center; justify-content: center; gap: 40px;
  }
  .card {
    position: relative; width: 540px; height: 309px;
    border-radius: 16px; overflow: hidden;
    box-shadow: 0 10px 30px rgba(0,0,0,.55);
  }
  .card-band { position: absolute; left: 0; bottom: 0; width: 100%; height: 40px; }

  /* Front */
  .card-front { background: var(--photo-dark); }
  .front-photo {
    position: absolute; inset: 0;
    background:
      radial-gradient(ellipse at 70% 30%, var(--photo-mid) 0%, transparent 60%),
      linear-gradient(135deg, #2a2725 0%, var(--photo-dark) 55%, #141312 100%);
  }
  .front-brand {
    position: absolute; left: 0; right: 0; top: 112px;
    display: flex; align-items: center; justify-content: center; gap: 14px;
  }
  .brand-mark { width: 34px; height: 34px; background: var(--blue); flex: none; }
  .brand-name {
    color: var(--blue); font-weight: 700; font-size: 40px;
    letter-spacing: 1px; line-height: 1; white-space: nowrap;
  }

  /* Back */
  .card-back { background: var(--card); }
  .back-brand {
    position: absolute; left: 28px; top: 120px;
    display: flex; align-items: center; gap: 8px;
  }
  .back-brand .brand-mark { width: 20px; height: 20px; }
  .back-brand .brand-name { font-size: 21px; letter-spacing: .5px; }
  .divider {
    position: absolute; left: 286px; top: 66px; width: 1px; height: 130px;
    background: var(--muted); transform: rotate(-12deg); opacity: .8;
  }
  .contact { position: absolute; left: 308px; top: 50px; color: var(--white); }
  .person-name { font-weight: 700; font-size: 24px; line-height: 1.1; white-space: nowrap; }
  .person-name .first { color: var(--blue); }
  .person-name .last { color: var(--grey); }
  .person-role { font-weight: 600; font-size: 13px; margin-top: 3px; }
  .contact-list { list-style: none; margin-top: 16px; }
  .contact-list li {
    display: flex; align-items: center; gap: 8px;
    font-size: 12px; line-height: 1.75; white-space: nowrap;
  }
  .contact-list svg { width: 12px; height: 12px; flex: none; }
  .address {
    position: absolute; left: 0; right: 0; bottom: 54px;
    text-align: center; color: var(--white); font-size: 13px;
  }
</style>
</head>
<body>
<main class="sheet">

  <section class="card card-front" aria-label="Card front">
    <div class="front-photo" role="img" aria-label="Dimly lit office interior photograph"></div>
    <div class="front-brand">
      <span class="brand-mark"></span>
      <span class="brand-name">RWT Fittings Ltd</span>
    </div>
    <svg class="card-band" viewBox="0 0 540 40" preserveAspectRatio="none" aria-hidden="true">
      <polygon points="300,14 540,6 540,40 300,40" fill="var(--grey)"/>
      <polygon points="0,24 270,24 310,40 0,40" fill="var(--blue)"/>
      <polygon points="270,24 310,14 330,40 310,40" fill="var(--grey)"/>
    </svg>
  </section>

  <section class="card card-back" aria-label="Card back">
    <div class="back-brand">
      <span class="brand-mark"></span>
      <span class="brand-name">RWT Fittings Ltd</span>
    </div>
    <div class="divider"></div>
    <div class="contact">
      <h1 class="person-name"><span class="first">Marco</span> <span class="last">Peltieri</span></h1>
      <p class="person-role">Owner &amp; Manager</p>
      <ul class="contact-list">
        <li>
          <svg viewBox="0 0 24 24" aria-hidden="true"><path fill="var(--blue)" d="M6.6 10.8a15 15 0 0 0 6.6 6.6l2.2-2.2c.3-.3.7-.4 1-.2 1.1.4 2.3.6 3.6.6.6 0 1 .4 1 1V20c0 .6-.4 1-1 1A17 17 0 0 1 3 4c0-.6.4-1 1-1h3.5c.6 0 1 .4 1 1 0 1.3.2 2.5.6 3.6.1.3 0 .7-.2 1z"/></svg>
          (604) 551-8293
        </li>
        <li>
          <svg viewBox="0 0 24 24" aria-hidden="true"><path fill="var(--blue)" d="M2 5h20v14H2zm2 2v.5l8 5 8-5V7zm0 2.8V17h16V9.8l-8 5z"/></svg>
          RWTFittings@mailbox-demo.com
        </li>
        <li>
          <svg viewBox="0 0 24 24" aria-hidden="true"><circle cx="12" cy="12" r="9" fill="none" stroke="var(--blue)" stroke-width="2.4"/><path d="M3 12h18M12 3c3 3 3 15 0 18M12 3c-3 3-3 15 0 18" fill="none" stroke="var(--blue)" stroke-width="1.6"/></svg>
          www.rwtfittings-demo.com
        </li>
      </ul>
    </div>
    <p class="address">1407-5194 Linden Row Burnaby BC, V5H 2K9</p>
    <svg class="card-band" viewBox="0 0 540 40" preserveAspectRatio="none" aria-hidden="true">
      <polygon points="300,14 540,6 540,40 300,40" fill="var(--grey)"/>
      <polygon points="0,24 270,24 310,40 0,40" fill="var(--blue)"/>
      <polygon points="270,24 310,14 330,40 310,40" fill="var(--grey)"/>
    </svg>
  </section>

</main>
</body>
</html>
```